New Business Card Design Project

I need a design for business cards, i am an electrical business called "Corvane Electrical and Communications" i need the cards to be double sided with the company logo on the back (attached) the front needs to say my company name, web site, email address, telephone number, and ABN number and electrical license number. I am open to different arrangements of the information but would like the background to be incorporating something electrical or something that looks smart. open to all additional ideas also.

The company colours are orange and grey see logo attached.

Business Name: Corvane Electrical and Communications
Website: corvaneelectricalandcomms.example.com.au
Email: brent@corvaneelectricalandcomms.example.com.au
Telephone(mobile): 0481209736
ABN: 71208349162
Lic No: 418273D

Target Market(s)

Business entities, Project Managers, Accounts, Clients

Industry/Entity Type

Electrician

Contact Information for Business Card

I need a design for business cards, i am an electrical business called "Corvane Electrical and Communications" i need the cards to be double sided with the company logo on the back (attached) the front needs to say my company name

Font styles to use
Serif
Sans Serif

Colors
f37122
5c5c5c

Requirements
Must have
• Must have the Logo on the back open to different ways of it being on the back but had in mind to keep it central but again open to other options
Nice to have
• A real modern cool background that is eye catching yet contemporary
Should not have
• No backgrounds of a light bulb or plug or anything like that

```html
<!DOCTYPE html>
<html lang="en">
<head>
<meta charset="utf-8">
<title>Corvane Electrical and Communications – Business Card</title>
<link rel="stylesheet" href="https://fonts.googleapis.com/css2?family=Exo+2:wght@400;500;700&display=swap">
<style>
  :root {
    --orange: #f37122;
    --grey: #5c5c5c;
    --text-dark: #4a4a4a;
    --card-dark: #1d1d1f;
    --card-mid: #3b3b3e;
    --panel-light: #f3f3f3;
    --panel-shade: #d9d9d9;
    --brand-light: #d6d6d6;
    --page-bg: #e8e6e3;
  }
  * { margin: 0; padding: 0; box-sizing: border-box; }
  html, body {
    width: 1200px;
    height: 969px;
    overflow: hidden;
    background: var(--page-bg);
    font-family: "Exo 2", Arial, sans-serif;
  }
  .business-card {
    position: absolute;
    left: 100px;
    top: 203px;
    width: 1000px;
    height: 562px;
    border-radius: 34px;
    overflow: hidden;
    background: linear-gradient(180deg, var(--card-mid) 0%, var(--card-dark) 55%, #2a2a2c 100%);
    box-shadow: 0 18px 40px rgba(0, 0, 0, 0.25);
  }
  .card-shapes {
    position: absolute;
    inset: 0;
  }
  .contact-block {
    position: absolute;
    left: 34px;
    top: 250px;
    color: var(--text-dark);
  }
  .person-name {
    font-size: 35px;
    font-weight: 700;
    color: var(--orange);
    letter-spacing: 1px;
    line-height: 1;
  }
  .person-title {
    font-size: 25px;
    font-weight: 400;
    color: var(--grey);
    margin-top: 10px;
    letter-spacing: 0.5px;
  }
  .registration {
    margin-top: 28px;
    font-size: 25px;
    line-height: 36px;
    color: var(--grey);
  }
  .contact-list {
    list-style: none;
    margin-top: 20px;
    font-size: 19px;
    color: var(--grey);
  }
  .contact-list li {
    display: flex;
    align-items: center;
    height: 38px;
  }
  .contact-list li.phone { font-size: 25px; }
  .contact-icon {
    width: 22px;
    height: 22px;
    margin-right: 12px;
    flex: none;
  }
  .brand-name {
    position: absolute;
    right: 40px;
    top: 70px;
    text-align: right;
    color: var(--brand-light);
    font-weight: 500;
  }
  .brand-name .brand-main {
    display: block;
    font-size: 82px;
    letter-spacing: 6px;
    line-height: 1;
  }
  .brand-name .brand-sub {
    display: block;
    font-size: 21px;
    letter-spacing: 2px;
    margin-top: 12px;
  }
</style>
</head>
<body>
  <div class="business-card">
    <svg class="card-shapes" width="1000" height="562" viewBox="0 0 1000 562">
      <defs>
        <linearGradient id="panelFill" x1="0" y1="0" x2="0" y2="1">
          <stop offset="0" stop-color="var(--panel-light)"/>
          <stop offset="1" stop-color="var(--panel-shade)"/>
        </linearGradient>
      </defs>
      <circle cx="215" cy="490" r="338" fill="none" stroke="#111" stroke-width="6"/>
      <circle cx="215" cy="490" r="330" fill="url(#panelFill)" stroke="var(--orange)" stroke-width="5"/>
    </svg>

    <div class="brand-name">
      <span class="brand-main">CORVANE</span>
      <span class="brand-sub">ELECTRICAL &amp; COMMUNICATIONS</span>
    </div>

    <div class="contact-block">
      <p class="person-name">DALE HOLLIS</p>
      <p class="person-title">CEO/FOUNDER</p>
      <p class="registration">ABN: 71208349162<br>Lic No: 418273D</p>
      <ul class="contact-list">
        <li class="phone">
          <svg class="contact-icon" viewBox="0 0 22 22"><rect x="5" y="1" width="12" height="20" rx="2.5" fill="none" stroke="var(--orange)" stroke-width="2.4"/><circle cx="11" cy="17" r="1.3" fill="var(--orange)"/></svg>
          0481209736
        </li>
        <li class="email">
          <svg class="contact-icon" viewBox="0 0 22 22"><rect x="1" y="5" width="20" height="13" fill="var(--orange)"/><path d="M1 5 L11 13 L21 5" fill="none" stroke="var(--panel-light)" stroke-width="1.6"/></svg>
          brent@corvaneelectricalandcomms.example.com.au
        </li>
        <li class="website">
          <svg class="contact-icon" viewBox="0 0 22 22"><circle cx="11" cy="11" r="9.5" fill="var(--orange)"/><path d="M1.5 11 H20.5 M11 1.5 C6 6 6 16 11 20.5 M11 1.5 C16 6 16 16 11 20.5" fill="none" stroke="var(--panel-light)" stroke-width="1.3"/></svg>
          corvaneelectricalandcomms.example.com.au
        </li>
      </ul>
    </div>
  </div>
</body>
</html>
```